Law Offices business card

Hi there, I'll need business card for the Law Offices of Colin Matheny. The information must convey his strategic approach and quick resolution to complex business litigation needs. Please emphasize Civil Litigation, Corporate Law, Business Governance and Real Estate Law. Colin has over 25 years of experience in these fields.The card should be modern and edgy and the message should be clear. Please consult his current website for ideas.

```html
<!DOCTYPE html>
<html lang="en">
<head>
<meta charset="utf-8">
<title>Law Offices of Colin Matheny — Business Card</title>
<link href="https://fonts.googleapis.com/css2?family=Tinos:wght@400;700&family=Noto+Sans:wght@400&display=swap" rel="stylesheet">
<style>
  :root {
    --backdrop: #3a322d;
    --card: #161616;
    --card-edge: #0c0c0c;
    --ink: #f4f4f4;
    --ink-soft: #d9d9d9;
    --rule: #bdbdbd;
    --bullet: #9a9a9a;
  }
  * { box-sizing: border-box; margin: 0; padding: 0; }
  html, body { width: 1200px; height: 780px; overflow: hidden; }
  body {
    background: var(--backdrop);
    position: relative;
    font-family: "Noto Sans", Verdana, sans-serif;
    color: var(--ink);
  }
  .card {
    position: absolute;
    top: 240px;
    width: 525px;
    height: 300px;
    background: linear-gradient(160deg, #1c1c1c 0%, var(--card) 60%, #121212 100%);
    border: 1px solid var(--card-edge);
    border-radius: 3px;
    box-shadow: 0 10px 24px rgba(0,0,0,.35);
    overflow: hidden;
  }
  .card--front { left: 50px; }
  .card--back { left: 625px; }

  .attorney-name {
    position: absolute; left: 40px; top: 30px;
    font-family: "Tinos", "Times New Roman", serif;
    font-weight: 700; font-size: 27px; letter-spacing: .2px;
  }
  .attorney-title {
    position: absolute; left: 40px; top: 63px;
    font-size: 13px; color: var(--ink-soft);
  }
  .firm-name {
    position: absolute; left: 40px; top: 86px;
    font-family: "Tinos", "Times New Roman", serif;
    font-weight: 700; font-size: 23px;
  }
  .contact-list {
    position: absolute; left: 40px; top: 138px;
    list-style: none;
  }
  .contact-item {
    display: flex; align-items: center; gap: 10px;
    height: 24px; font-size: 14px; color: var(--ink);
  }
  .contact-icon { width: 13px; height: 13px; flex: none; }

  .service-rule {
    position: absolute; left: 0; right: 0; top: 40px;
    height: 1px; background: var(--rule);
  }
  .service-heading {
    position: absolute; left: 70px; top: 52px;
    font-family: "Tinos", "Times New Roman", serif;
    font-size: 38px; font-weight: 400;
  }
  .service-list {
    position: absolute; left: 40px; top: 118px;
    list-style: none;
  }
  .service-item {
    display: flex; align-items: center; gap: 14px;
    height: 30px; font-size: 18px; letter-spacing: .3px;
  }
  .service-bullet {
    width: 7px; height: 7px; border-radius: 50%;
    background: var(--bullet); border: 1px solid #d0d0d0; flex: none;
  }
</style>
</head>
<body>

<section class="card card--front" aria-label="Card front">
  <h1 class="attorney-name">Colin Matheny</h1>
  <p class="attorney-title">Attorney</p>
  <h2 class="firm-name">Law offices of Colin Matheny, P.A.</h2>
  <ul class="contact-list">
    <li class="contact-item">
      <svg class="contact-icon" viewBox="0 0 13 13" aria-hidden="true"><rect width="13" height="13" rx="1.5" fill="#f4f4f4"/><path d="M4 3 l1.3 0 l.6 2 l-.9.7 q.8 1.7 2.3 2.4 l.7-.9 l2 .6 l0 1.3 q-4.8 .3-6-6.1z" fill="#161616"/></svg>
      <span>555-210-4873</span>
    </li>
    <li class="contact-item">
      <svg class="contact-icon" viewBox="0 0 13 13" aria-hidden="true"><rect width="13" height="13" rx="1.5" fill="#f4f4f4"/><rect x="4.3" y="2.5" width="4.4" height="8" rx=".8" fill="#161616"/><rect x="5.1" y="3.5" width="2.8" height="4.8" fill="#f4f4f4"/></svg>
      <span>555-306-9152</span>
    </li>
    <li class="contact-item">
      <svg class="contact-icon" viewBox="0 0 13 13" aria-hidden="true"><rect width="13" height="13" rx="1.5" fill="#f4f4f4"/><circle cx="6.5" cy="6.5" r="3.8" fill="none" stroke="#161616" stroke-width="1"/><path d="M2.7 6.5h7.6M6.5 2.7q-2.4 3.8 0 7.6M6.5 2.7q2.4 3.8 0 7.6" fill="none" stroke="#161616" stroke-width=".8"/></svg>
      <span>www.mathenylaw.com</span>
    </li>
    <li class="contact-item">
      <svg class="contact-icon" viewBox="0 0 13 13" aria-hidden="true"><rect width="13" height="13" rx="1.5" fill="#f4f4f4"/><rect x="2.5" y="3.8" width="8" height="5.6" fill="none" stroke="#161616" stroke-width="1"/><path d="M2.5 3.8l4 3 4-3" fill="none" stroke="#161616" stroke-width="1"/></svg>
      <span>colin@mathenylaw.com</span>
    </li>
    <li class="contact-item">
      <svg class="contact-icon" viewBox="0 0 13 13" aria-hidden="true"><rect width="13" height="13" rx="1.5" fill="#f4f4f4"/><path d="M6.5 11 q-3.2-3.8-3.2-5.6 a3.2 3.2 0 0 1 6.4 0 q0 1.8-3.2 5.6z" fill="#161616"/><circle cx="6.5" cy="5.4" r="1.1" fill="#f4f4f4"/></svg>
      <span>118B Harbor Avenue Palm Shores, Florida 33410</span>
    </li>
  </ul>
</section>

<section class="card card--back" aria-label="Card back">
  <div class="service-rule"></div>
  <h2 class="service-heading">Service</h2>
  <ul class="service-list">
    <li class="service-item"><span class="service-bullet"></span>Civil Litigation</li>
    <li class="service-item"><span class="service-bullet"></span>Corporate Law</li>
    <li class="service-item"><span class="service-bullet"></span>Real Estate Law</li>
    <li class="service-item"><span class="service-bullet"></span>Business Governance</li>
  </ul>
</section>

</body>
</html>
```